Business card for medical clinic

I need an upmarket, modern medical/health business card for my clinic

Contact Information for Business Card

name, address, email, qr code

```html
<!DOCTYPE html>
<html lang="en">
<head>
<meta charset="utf-8">
<title>Cordia Health Partners – Business Card</title>
<link rel="stylesheet" href="https://fonts.googleapis.com/css2?family=Montserrat:wght@400;500;700&display=swap">
<style>
  :root {
    --stage: #3a3a3a;
    --blue-deep: #114a6e;
    --blue-mid: #176391;
    --blue-light: #2596c8;
    --ink: #1e1e1e;
    --paper: #ffffff;
    --accent: #1a6fa3;
  }
  * { margin: 0; padding: 0; box-sizing: border-box; }
  html, body { width: 1200px; height: 689px; overflow: hidden; }
  body {
    background: var(--stage);
    font-family: "Montserrat", sans-serif;
    position: relative;
  }
  .card {
    position: absolute;
    top: 190px;
    width: 540px;
    height: 309px;
    border-radius: 22px;
    overflow: hidden;
  }
  .card--front {
    left: 40px;
    background: linear-gradient(150deg, var(--blue-deep) 0%, var(--blue-mid) 50%, var(--blue-light) 100%);
    display: flex;
    align-items: center;
    justify-content: center;
  }
  .card--back { left: 620px; background: var(--paper); }

  .brand { display: flex; align-items: center; gap: 14px; }
  .brand__dot {
    border-radius: 50%;
    border: 4px solid currentColor;
    flex: none;
  }
  .brand__name {
    font-weight: 500;
    letter-spacing: 0.12em;
    text-transform: uppercase;
    line-height: 1.15;
  }
  .card--front .brand { color: var(--paper); }
  .card--front .brand__dot { width: 64px; height: 64px; }
  .card--front .brand__name { font-size: 25px; }

  .card--back .brand {
    position: absolute; left: 34px; top: 40px; color: var(--accent); gap: 10px;
  }
  .card--back .brand__dot { width: 36px; height: 36px; border-width: 3px; }
  .card--back .brand__name { font-size: 14px; }

  .person {
    position: absolute; right: 40px; top: 48px; text-align: right;
  }
  .person__name {
    font-weight: 700; font-size: 19px; color: var(--accent); letter-spacing: 0.02em;
  }
  .person__title { font-size: 12px; color: var(--ink); margin-top: 2px; }
  .person-bar {
    position: absolute; right: 0; top: 44px; width: 14px; height: 42px;
    background: linear-gradient(90deg, var(--blue-deep), var(--blue-light));
  }

  .address {
    position: absolute; left: 34px; top: 150px;
    font-size: 13px; line-height: 1.45; color: var(--ink);
  }
  .contacts {
    position: absolute; left: 34px; top: 208px; list-style: none;
    font-size: 13px; line-height: 1.75; color: var(--ink);
  }
  .contacts li { display: flex; align-items: center; gap: 8px; }
  .contacts svg { width: 12px; height: 12px; fill: var(--accent); flex: none; }
</style>
</head>
<body>
  <section class="card card--front" aria-label="Card front">
    <div class="brand">
      <span class="brand__dot"></span>
      <span class="brand__name">Cordia Health<br>Partners</span>
    </div>
  </section>

  <section class="card card--back" aria-label="Card back">
    <div class="brand">
      <span class="brand__dot"></span>
      <span class="brand__name">Cordia Health<br>Partners</span>
    </div>

    <div class="person">
      <p class="person__name">DANIEL REED</p>
      <p class="person__title">Managing Director</p>
    </div>
    <span class="person-bar"></span>

    <p class="address">Your address, City<br>State, Zip 1234</p>

    <ul class="contacts">
      <li>
        <svg viewBox="0 0 24 24" aria-hidden="true"><path d="M6.6 10.8a15.1 15.1 0 0 0 6.6 6.6l2.2-2.2a1 1 0 0 1 1-.25 11.4 11.4 0 0 0 3.6.57 1 1 0 0 1 1 1V20a1 1 0 0 1-1 1A17 17 0 0 1 3 4a1 1 0 0 1 1-1h3.5a1 1 0 0 1 1 1c0 1.25.2 2.45.57 3.57a1 1 0 0 1-.25 1z"/></svg>
        123 456 789
      </li>
      <li>
        <svg viewBox="0 0 24 24" aria-hidden="true"><path d="M2 5h20v14H2zm2 2v.5l8 5 8-5V7l-8 5z"/></svg>
        info@youremail.com
      </li>
      <li>
        <svg viewBox="0 0 24 24" aria-hidden="true"><path d="M12 2a10 10 0 1 0 0 20 10 10 0 0 0 0-20zm6.9 6h-3a15.6 15.6 0 0 0-1.4-3.6A8 8 0 0 1 18.9 8zM12 4a14 14 0 0 1 1.9 4h-3.8A14 14 0 0 1 12 4zM4.3 14a8 8 0 0 1 0-4h3.4a16 16 0 0 0 0 4zm.8 2h3a15.6 15.6 0 0 0 1.4 3.6A8 8 0 0 1 5.1 16zm3-8h-3a8 8 0 0 1 4.4-3.6A15.6 15.6 0 0 0 8.1 8zM12 20a14 14 0 0 1-1.9-4h3.8A14 14 0 0 1 12 20zm2.3-6H9.7a14.6 14.6 0 0 1 0-4h4.6a14.6 14.6 0 0 1 0 4zm.2 5.6a15.6 15.6 0 0 0 1.4-3.6h3a8 8 0 0 1-4.4 3.6zm1.8-5.6a16 16 0 0 0 0-4h3.4a8 8 0 0 1 0 4z"/></svg>
        www.yourwebsite.com
      </li>
    </ul>
  </section>
</body>
</html>
```